Brivolt Technologies business card design

We need a business card designed with our new logo. it would be great if the card could communicate it is a technology based company.

Target Market(s)

system integrators

Industry/Entity Type

technology, IOT

Contact Information for Business Card

Name, designation, Address, telephone number, email address

Requirements
Must have
• logo and company name
Nice to have
• something to do with technology

```html
<!DOCTYPE html>
<html lang="en">
<head>
<meta charset="utf-8">
<title>Brivolt Technologies – Business Card</title>
<link rel="stylesheet" href="https://fonts.googleapis.com/css2?family=Arimo:wght@400;700&display=swap">
<style>
  :root {
    --stage: #3a3236;
    --card-dark: #333333;
    --card-light: #ffffff;
    --ink: #333333;
    --accent: #f7931e;
  }
  * { box-sizing: border-box; margin: 0; padding: 0; }
  html, body { width: 1200px; height: 912px; overflow: hidden; }
  body {
    background: var(--stage);
    font-family: "Arimo", Arial, sans-serif;
    position: relative;
  }
  .card {
    position: absolute;
    width: 630px;
    height: 360px;
    border-radius: 22px;
    box-shadow: 0 12px 30px rgba(0,0,0,0.45);
    overflow: hidden;
  }

  /* Back of card */
  .card-back {
    left: 60px; top: 60px;
    background: var(--card-dark);
    display: flex; align-items: center; justify-content: center;
  }
  .brand { display: flex; align-items: center; gap: 14px; }
  .brand-square { width: 30px; height: 30px; background: var(--accent); flex: none; }
  .brand-name {
    font-weight: 700;
    font-size: 40px;
    letter-spacing: 1px;
    color: var(--accent);
    white-space: nowrap;
  }

  /* Front of card */
  .card-front {
    left: 510px; top: 500px;
    background: var(--card-light);
  }
  .front-brand {
    position: absolute; left: 40px; top: 38px;
    font-weight: 700;
    font-size: 30px;
    line-height: 1.05;
    letter-spacing: 1px;
    text-transform: uppercase;
    color: var(--ink);
  }
  .front-feature {
    position: absolute;
    right: 60px; top: 80px;
    width: 190px; height: 190px;
    background: var(--ink);
  }

  .details {
    position: absolute; left: 0; top: 126px;
    padding-left: 64px;
    width: 360px;
  }
  .name-block { position: relative; margin-bottom: 16px; }
  .name-block::before {
    content: ""; position: absolute;
    left: -64px; top: 2px;
    width: 26px; height: 50px;
    background: var(--accent);
  }
  .person-name {
    font-weight: 700; font-size: 24px;
    color: var(--accent); letter-spacing: 0.5px;
    text-transform: uppercase;
    white-space: nowrap;
  }
  .person-title { font-size: 16px; color: var(--ink); margin-top: 3px; }
  .address { font-size: 16px; color: var(--ink); line-height: 1.3; margin-bottom: 14px; font-style: normal; }
  .contact-list { list-style: none; }
  .contact-list li {
    display: flex; align-items: center; gap: 10px;
    font-size: 16px; color: var(--ink); line-height: 1.55;
    white-space: nowrap;
  }
  .contact-list svg { width: 15px; height: 15px; flex: none; }
</style>
</head>
<body>

  <section class="card card-back" aria-label="Card back">
    <div class="brand">
      <span class="brand-square"></span>
      <span class="brand-name">Brivolt Technologies</span>
    </div>
  </section>

  <section class="card card-front" aria-label="Card front">
    <p class="front-brand">Brivolt<br>Technologies</p>
    <span class="front-feature" aria-hidden="true"></span>

    <div class="details">
      <div class="name-block">
        <p class="person-name">Daniel Harwood</p>
        <p class="person-title">CEO/Founder</p>
      </div>
      <address class="address">
        2180 Linden Avenue<br>
        Northvale AB 4416
      </address>
      <ul class="contact-list">
        <li>
          <svg viewBox="0 0 16 16" aria-hidden="true"><path fill="#f7931e" d="M3.5 1.5l2.5 3-1.5 1.5c.8 1.8 2.2 3.2 4 4l1.5-1.5 3 2.5-1.5 2.5C6.5 13 3 9.5 1 4z"/></svg>
          (123) 480-3175
        </li>
        <li>
          <svg viewBox="0 0 16 16" aria-hidden="true"><rect x="1" y="3" width="14" height="10" fill="#f7931e"/><path d="M1 3l7 6 7-6" stroke="#fff" stroke-width="1.4" fill="none"/></svg>
          info@brivolttechnologies.com
        </li>
        <li>
          <svg viewBox="0 0 16 16" aria-hidden="true"><g fill="none" stroke="#f7931e" stroke-width="1.4"><circle cx="8" cy="8" r="6.5"/><ellipse cx="8" cy="8" rx="2.8" ry="6.5"/><path d="M1.5 8h13M2.5 4.8h11M2.5 11.2h11"/></g></svg>
          www.brivolttechnologies.com
        </li>
      </ul>
    </div>
  </section>

</body>
</html>
```